I have a website called Okenta Holdings (okentaholdings.com) that I would like to have redesigned. Most of the content is already created, but I need a new design. You can also see my other website at brambleacres.com. I am open to a new logo or modifying the current logo if you have a good idea. Please feel free to use other images for the home page (and maybe some other locations) if you feel they provide a better look and feel to the website. I prefer a modern look.

Important: You do not have to use the images I've provided for the home page. Feel free to find your own stock photos. You don't have to pay for them unless I select your design.

1) Please use wix.com to make your changes so that I can edit it later.
2) I will need all the graphics files to be saved so I can dowload it for later.
3) I will be adding more content to the site later.
4) This site will likely be transferred over to brambleacres.com so if you make a logo please make one for Okenta Holdings and one for Bramble Acres.
5) You can use other images that you feel would help the look and feel of the website.

```html
<!DOCTYPE html>
<html lang="en">
<head>
<meta charset="utf-8">
<title>Okenta Holdings</title>
<link href="https://fonts.googleapis.com/css2?family=Lato:ital,wght@0,400;0,700;1,400&family=Poppins:wght@400;500&display=swap" rel="stylesheet">
<style>
:root{
  --navy:#1d3557;
  --deep:#2b4a6b;
  --blue:#5b9ad5;
  --btn:#5b95d0;
  --ink:#333b45;
  --text:#4a4f57;
  --pale:#e1ebf6;
  --white:#ffffff;
  --submit:#0f2a4d;
  --brand:#3f72a8;
}
*{box-sizing:border-box;margin:0;padding:0}
html,body{width:1200px;height:4074px;overflow:hidden}
body{position:relative;font-family:"Lato",sans-serif;color:var(--text);background:var(--white)}
.abs{position:absolute}
.btn{position:absolute;display:flex;align-items:center;justify-content:center;background:var(--btn);color:var(--white);font-weight:700;font-size:18px;font-family:"Lato",sans-serif;text-decoration:none}

/* brand */
.brand{position:absolute;display:flex;align-items:center;gap:14px;font-family:"Lato",sans-serif;font-weight:700;color:var(--brand);white-space:nowrap;line-height:1}
.brand-mark{width:46px;height:46px;background:var(--brand);border-radius:50%;flex:none}
.header-brand{left:76px;top:37px;font-size:36px}
.footer-brand{left:82px;top:3665px;font-size:34px}

/* header */
.site-header{left:0;top:0;width:1200px;height:120px;background:var(--white)}
.nav{position:absolute;right:76px;top:51px;display:flex;gap:38px;font-size:17px;color:var(--navy);font-weight:700}
.nav .active{color:var(--brand)}

/* hero */
.hero{left:0;top:120px;width:1200px;height:723px;background:linear-gradient(180deg,#8e7fb8 0%,#d59aa7 28%,#e8a97a 45%,#8d8a9e 62%,#5f6773 80%,#3d5a3a 100%)}
.hero-small{left:76px;top:325px;font-size:58px;color:var(--white);font-weight:400;line-height:1}
.hero-title{left:76px;top:382px;font-size:86px;color:var(--white);font-weight:700;line-height:1;white-space:nowrap}
.hero-sub{left:76px;top:481px;width:520px;font-size:22px;line-height:33px;color:var(--white);font-weight:700}

/* about */
.about-band{left:0;top:843px;width:329px;height:583px;background:var(--deep)}
.about-photo{left:87px;top:912px;width:500px;height:445px;background:linear-gradient(135deg,#b9c3cc,#6f7a86 60%,#3b4450)}
.about-title{left:616px;top:914px;font-size:52px;line-height:58px;color:var(--navy);font-weight:400}
.about-text{left:616px;top:1048px;width:510px;font-size:16px;line-height:31.5px;color:var(--text)}

/* strategy */
.strategy{left:0;top:1426px;width:1200px;height:524px;background:linear-gradient(180deg,#d6e5f3,#e4eef8)}
.strategy-title{left:0;top:1468px;width:1200px;text-align:center;font-size:52px;color:var(--ink);font-weight:400}
.card{position:absolute;top:1557px;width:329px;height:236px;background:var(--white);padding:36px 20px 0 20px}
.card h3{font-size:24px;line-height:29px;color:var(--navy);font-weight:700;width:200px}
.card ul{list-style:none;margin-top:12px}
.card li{display:flex;align-items:center;gap:14px;font-size:16px;line-height:33px;color:var(--text)}
.card li svg{flex:none}
.card .icon{position:absolute;right:20px;top:24px}

/* offering */
.offering{left:0;top:1950px;width:1200px;height:675px;background:var(--blue)}
.offer-photo{left:74px;top:2033px;width:601px;height:510px;background:linear-gradient(160deg,#c6d2de 0%,#b8b4ad 45%,#6e6b6b 80%,#8e8c88)}
.offer-card{left:587px;top:2073px;width:539px;height:431px;background:var(--white);padding:36px 27px}
.offer-card h2{font-size:52px;font-weight:400;color:var(--navy);line-height:60px}
.offer-card h4{font-size:29px;font-weight:700;color:var(--blue);margin-top:12px}
.offer-card p{font-size:18px;line-height:38px;color:var(--text)}
.offer-card .facts{margin-top:8px}

/* testimonials */
.say-title{left:0;top:2680px;width:1200px;text-align:center;font-size:52px;color:var(--navy);font-weight:400}
.say-quote{left:270px;top:2773px;width:660px;text-align:center;font-style:italic;font-size:16px;line-height:31.5px;color:var(--text)}
.say-name{left:0;top:2888px;width:1200px;text-align:center;font-size:17px;color:var(--blue);font-weight:700}
.dots{left:0;top:2973px;width:1200px;display:flex;justify-content:center;gap:15px}
.dots span{width:9px;height:9px;border-radius:50%;background:#b7bcc4}
.dots span:first-child{background:#111}

.quote-band{left:0;top:3062px;width:1200px;height:463px;background:linear-gradient(180deg,#355d91,#2b4c7d 60%,#2d4a73)}
.band-quote{left:180px;top:3208px;width:840px;text-align:center;font-size:23px;line-height:40px;color:var(--white)}
.band-name{left:0;top:3346px;width:1200px;text-align:center;font-size:19px;color:var(--white);font-weight:700}

/* footer */
.footer{left:0;top:3525px;width:1200px;height:478px;background:var(--pale)}
.address{left:74px;top:3762px;font-family:"Poppins",sans-serif;font-size:16px;line-height:27px;color:#1c2430}
.address .gap{margin-top:8px}
.field{position:absolute;border-bottom:1px solid #8d97a3;font-family:"Poppins",sans-serif;font-size:14px;color:#1c2430;padding:0 2px 10px}
.submit{left:616px;top:3855px;width:135px;height:45px;background:var(--submit);color:var(--white);font-family:"Poppins",sans-serif;font-size:15px;display:flex;align-items:center;justify-content:center}
.bottom-bar{left:0;top:4003px;width:1200px;height:71px;background:var(--pale);border-top:1px solid #c9d3de}
.copyright{left:74px;top:4026px;font-family:"Poppins",sans-serif;font-size:14px;color:#1c2430}
.social{right:74px;top:4021px;display:flex;gap:22px}
.social span{width:30px;height:30px;border-radius:50%;background:var(--navy)}
</style>
</head>
<body>

<header class="abs site-header">
  <nav class="nav">
    <span class="active">Home</span><span>Strategy</span><span>About Us</span><span>Current Offerings</span><span>Contact</span>
  </nav>
</header>
<div class="brand header-brand"><span class="brand-mark"></span>Okenta Holdings</div>

<section class="abs hero" role="img" aria-label="City skyline at sunset seen from a hillside with trees in the foreground"></section>
<div class="abs hero-small">Welcome to</div>
<h1 class="abs hero-title">Okenta Holdings</h1>
<p class="abs hero-sub">Neque porro quisquam est qui dolorem ipsum quia dolor sit ametconsectetur.</p>
<a class="btn" style="left:76px;top:578px;width:161px;height:50px">Read More</a>

<div class="abs about-band"></div>
<div class="abs about-photo" role="img" aria-label="Portrait of the firm's principal in a suit in front of city buildings"></div>
<h2 class="abs about-title">About<br>Okenta Holdings</h2>
<div class="abs about-text">
  <p>Bramble Acres is a private real estate firm that specializes in the procurement, development, management, and disposition of various commercial real estate asset types including multifamily, retail, office, hospitality, industrial and self-storage.</p>
  <p>The firm effectuates its strategy by providing equity to developers and sponsors through a joint venture partnership arrangement with accredited investors, institutional funds, and family offices.</p>
</div>
<a class="btn" style="left:616px;top:1298px;width:144px;height:47px">Read More</a>

<section class="abs strategy" role="img" aria-label="Faded photo of a modern apartment courtyard with a pool"></section>
<h2 class="abs strategy-title">Strategy</h2>

<div class="card" style="left:74px">
  <svg class="icon" width="58" height="56" viewBox="0 0 58 56" fill="none" stroke="#5b95d0" stroke-width="2"><path d="M4 52h14V36H4zM22 52v-8l12-6h10"/><path d="M20 28l10-10 8 6 14-14M44 10h8v8"/></svg>
  <h3>Investment Focus</h3>
  <ul>
    <li><svg width="16" height="16" viewBox="0 0 16 16" fill="none" stroke="#4a4f57" stroke-width="1.4"><circle cx="8" cy="8" r="7"/><path d="M5 8.3l2 2 4-4"/></svg>Development</li>
    <li><svg width="16" height="16" viewBox="0 0 16 16" fill="none" stroke="#4a4f57" stroke-width="1.4"><circle cx="8" cy="8" r="7"/><path d="M5 8.3l2 2 4-4"/></svg>Value-Add Acquisition</li>
    <li><svg width="16" height="16" viewBox="0 0 16 16" fill="none" stroke="#4a4f57" stroke-width="1.4"><circle cx="8" cy="8" r="7"/><path d="M5 8.3l2 2 4-4"/></svg>Debt Financing</li>
  </ul>
</div>
<div class="card" style="left:436px">
  <svg class="icon" width="58" height="56" viewBox="0 0 58 56" fill="none" stroke="#5b95d0" stroke-width="2"><path d="M4 50V20h14v30M18 50V8h14v42"/><circle cx="42" cy="38" r="12"/><path d="M2 50h38"/></svg>
  <h3>Role of Bramble Acres</h3>
  <ul>
    <li><svg width="16" height="16" viewBox="0 0 16 16" fill="none" stroke="#4a4f57" stroke-width="1.4"><circle cx="8" cy="8" r="7"/><path d="M5 8.3l2 2 4-4"/></svg>Opportunity Procurement</li>
    <li><svg width="16" height="16" viewBox="0 0 16 16" fill="none" stroke="#4a4f57" stroke-width="1.4"><circle cx="8" cy="8" r="7"/><path d="M5 8.3l2 2 4-4"/></svg>Financial Underwriting</li>
    <li><svg width="16" height="16" viewBox="0 0 16 16" fill="none" stroke="#4a4f57" stroke-width="1.4"><circle cx="8" cy="8" r="7"/><path d="M5 8.3l2 2 4-4"/></svg>Capital Raising</li>
  </ul>
</div>
<div class="card" style="left:798px">
  <svg class="icon" width="58" height="58" viewBox="0 0 58 58" fill="none" stroke="#5b95d0" stroke-width="2"><path d="M4 56h50M10 56V22h14v34M24 56V4h20v52"/><path d="M30 12h3M37 12h3M30 22h3M37 22h3M30 32h3M37 32h3M30 42h3M37 42h3M15 30h4M15 40h4"/></svg>
  <h3>Product Types</h3>
  <ul>
    <li><svg width="16" height="16" viewBox="0 0 16 16" fill="none" stroke="#4a4f57" stroke-width="1.4"><circle cx="8" cy="8" r="7"/><path d="M5 8.3l2 2 4-4"/></svg>Retail</li>
    <li><svg width="16" height="16" viewBox="0 0 16 16" fill="none" stroke="#4a4f57" stroke-width="1.4"><circle cx="8" cy="8" r="7"/><path d="M5 8.3l2 2 4-4"/></svg>Office</li>
    <li><svg width="16" height="16" viewBox="0 0 16 16" fill="none" stroke="#4a4f57" stroke-width="1.4"><circle cx="8" cy="8" r="7"/><path d="M5 8.3l2 2 4-4"/></svg>Multifamily</li>
    <li><svg width="16" height="16" viewBox="0 0 16 16" fill="none" stroke="#4a4f57" stroke-width="1.4"><circle cx="8" cy="8" r="7"/><path d="M5 8.3l2 2 4-4"/></svg>Self-Storage</li>
  </ul>
</div>
<a class="btn" style="left:528px;top:1846px;width:144px;height:46px">Read More</a>

<section class="abs offering"></section>
<div class="abs offer-photo" role="img" aria-label="Modern brick and stone townhome building with red doors"></div>
<div class="abs offer-card">
  <h2>Current Offering</h2>
  <h4>Equity: Multifamily Development</h4>
  <div class="facts">
    <p>Willow Bend, Texas</p>
    <p>Raise Amount: $8,000,000</p>
    <p>Projected IRR: 20%</p>
    <p>Projected Multiple: 3.0x</p>
  </div>
</div>
<a class="btn" style="left:616px;top:2405px;width:144px;height:47px">Read More</a>

<h2 class="abs say-title">What Patients Say</h2>
<p class="abs say-quote">“ Sed ut perspiciatis unde omnis iste natus error sit voluptatem accusantium doloremque laudantium, totam rem aperiam, eaque ipsa quae ab illo inventore veritatis et quasi architecto beatae vitae dicta sunt explicabo.”</p>
<div class="abs say-name">Name Heading</div>
<div class="abs dots"><span></span><span></span><span></span><span></span></div>

<section class="abs quote-band" role="img" aria-label="Multi-storey apartment building under a blue tint"></section>
<p class="abs band-quote">“Sed ut perspiciatis unde omnis iste natus error sit voluptatem accusantium doloremque laudantium, totam rem aperiam, eaque ipsa quae ab illo inventore veritatis et quasi architecto beatae vitae dicta sunt”</p>
<div class="abs band-name">Name Heading</div>

<footer class="abs footer"></footer>
<div class="brand footer-brand"><span class="brand-mark"></span>Okenta Holdings</div>
<div class="abs address">
  <div>PO Box 48317</div>
  <div>Fairbrook, Texas 75460</div>
  <div class="gap">Tel:&nbsp; (214) 555-0173</div>
  <div class="gap">Mail: info@brambleacres.com</div>
</div>
<div class="field" style="left:616px;top:3657px;width:243px">Name</div>
<div class="field" style="left:884px;top:3657px;width:242px">Email</div>
<div class="field" style="left:616px;top:3708px;width:243px">Phone</div>
<div class="field" style="left:884px;top:3708px;width:242px">Subject</div>
<div class="field" style="left:616px;top:3758px;width:243px;height:74px">Message</div>
<div class="field" style="left:884px;top:3758px;width:242px;height:74px"></div>
<div class="abs submit">Submit</div>

<div class="abs bottom-bar"></div>
<div class="abs copyright">© 2022 CompanyName&nbsp; Name All rights reserved.</div>
<div class="abs social" aria-label="Social media links"><span></span><span></span><span></span><span></span></div>

</body>
</html>
```